Tallowood building company Business card design

I need a business card design for my company. I have a logo but dont have business cards with our logo..

www.tallowoodbuildingco.com.au

The logo is on the website

I need the same details as this design I have attached. we have changed the logo and colours. just like the website

Building

```html
<!DOCTYPE html>
<html lang="en">
<head>
<meta charset="utf-8">
<title>Tallowood Building – Business Card</title>
<link href="https://fonts.googleapis.com/css2?family=Tinos:ital@0;1&display=swap" rel="stylesheet">
<style>
  :root {
    --page: #ffffff;
    --stone: #bccbcc;
    --sky: #33a6f0;
    --band-1: #78b9e0;
    --band-2: #56afe8;
    --band-3: #45abec;
    --band-4: #3aa8ef;
    --ink-light: #ffffff;
    --serif: "Tinos", "Times New Roman", serif;
  }
  html, body {
    margin: 0;
    padding: 0;
    width: 1200px;
    height: 1000px;
    overflow: hidden;
    background: var(--page);
  }
  .canvas {
    position: relative;
    width: 1200px;
    height: 1000px;
  }
  .card {
    position: absolute;
    left: 68px;
    top: 205px;
    width: 1064px;
    height: 590px;
    background: var(--stone);
    overflow: hidden;
    font-family: var(--serif);
  }
  .card-waves {
    position: absolute;
    inset: 0;
    width: 100%;
    height: 100%;
  }
  .brand-mark {
    position: absolute;
    left: 140px;
    top: 60px;
    width: 170px;
    height: 170px;
    background: var(--sky);
  }
  .brand-name {
    position: absolute;
    left: 20px;
    top: 300px;
    width: 410px;
    margin: 0;
    text-align: center;
    color: var(--sky);
    font-size: 62px;
    font-weight: 400;
    line-height: 80px;
  }
  .brand-name span { display: block; }
  .holder-name {
    position: absolute;
    left: 838px;
    top: 92px;
    margin: 0;
    font-size: 38px;
    font-weight: 400;
    color: var(--ink-light);
    text-decoration: underline;
    text-decoration-thickness: 2px;
    text-underline-offset: 8px;
  }
  .contact {
    position: absolute;
    left: 650px;
    top: 206px;
    margin: 0;
    color: var(--ink-light);
    font-size: 26px;
    font-style: normal;
    line-height: 33px;
  }
  .contact-row { display: block; white-space: nowrap; }
  .contact-label {
    display: inline-block;
    width: 124px;
    font-style: italic;
  }
</style>
</head>
<body>
<main class="canvas">
  <section class="card" aria-label="Tallowood Building business card">
    <svg class="card-waves" viewBox="0 0 1064 590" aria-hidden="true">
      <path d="M487,0 C440,80 440,220 462,300 C485,400 480,520 410,590 L1064,590 L1064,0 Z" fill="var(--band-1)"/>
      <path d="M548,0 C505,100 505,230 527,320 C550,420 545,520 470,590 L1064,590 L1064,0 Z" fill="var(--band-2)"/>
      <path d="M628,0 C590,100 592,230 612,320 C635,420 630,520 560,590 L1064,590 L1064,0 Z" fill="var(--band-3)"/>
      <path d="M728,0 C690,100 692,230 712,320 C735,420 725,520 650,590 L1064,590 L1064,0 Z" fill="var(--band-4)"/>
      <path d="M830,0 C795,100 795,230 815,320 C838,420 828,520 760,590 L1064,590 L1064,0 Z" fill="var(--sky)"/>
    </svg>

    <div class="brand-mark" aria-hidden="true"></div>
    <h1 class="brand-name">
      <span>Tallowood</span>
      <span>Building</span>
    </h1>

    <h2 class="holder-name">Name </h2>

    <address class="contact">
      <span class="contact-row"><span class="contact-label">Address</span>:</span>
      <span class="contact-row">Unit 4 Level 2,</span>
      <span class="contact-row">27 Marri Ave,</span>
      <span class="contact-row">Hillcrest, WA 6031</span>
      <span class="contact-row"><span class="contact-label">Phone</span>: 9412 5730</span>
      <span class="contact-row"><span class="contact-label">Mob</span>: 0412586903 ( Dana )</span>
      <span class="contact-row"><span class="contact-label">Email</span>:</span>
      <span class="contact-row">info@tallowoodbuildingco.com.au</span>
      <span class="contact-row"><span class="contact-label">Web</span>:</span>
      <span class="contact-row">www.tallowoodbuildingco.com.au</span>
    </address>
  </section>
</main>
</body>
</html>
```